Road Construction Company needs business cards

We would like a new business card designed for our business.

We're a road construction company based in Qld, Australia.

Can the business card please have the following information on it.

Name: Warren Halbeck
Position: General Manager
Phone: 0472 915 348
Email: Warren.halbeck@tovrin.com.au
Address: 87 Marrow Ave, Pendlebay, QLD, 4023
Website: www.tovrin.com.au

Visually we'd like the card to be professional and simple.

Attached is our logo.

Our website is www.tovrin.com.au

Target Market(s)

Men aged 25-60

Contact Information for Business Card

As listed in project description

Font styles to use
Serif

Requirements
Must have
• Large logo on back of card

```html
<!DOCTYPE html>
<html lang="en">
<head>
<meta charset="utf-8">
<title>Tovrin Road Construction – Business Card</title>
<link href="https://fonts.googleapis.com/css2?family=Noto+Serif:wght@400;700&display=swap" rel="stylesheet">
<style>
  :root {
    --backdrop: #474747;
    --backdrop-deep: #3a3a3a;
    --card: #161616;
    --card-edge: #34a8dc;
    --brand-blue: #0b59a9;
    --accent-blue: #34a8dc;
    --ink-light: #f2f2f2;
    --emboss: #1f1f1f;
  }
  * { box-sizing: border-box; margin: 0; padding: 0; }
  html, body {
    width: 1200px;
    height: 801px;
    overflow: hidden;
  }
  body {
    background: radial-gradient(ellipse at 40% 30%, var(--backdrop) 0%, var(--backdrop-deep) 100%);
    font-family: "Noto Serif", Georgia, serif;
    position: relative;
  }
  .card {
    position: absolute;
    top: 245px;
    width: 540px;
    height: 310px;
    background: var(--card);
    border-radius: 16px;
    border-left: 3px solid var(--card-edge);
    border-bottom: 3px solid var(--card-edge);
    box-shadow: 0 18px 40px rgba(0,0,0,0.45);
    overflow: hidden;
  }
  .card--front { left: 40px; }
  .card--back { left: 620px; }

  .wordmark {
    position: absolute;
    font-weight: 700;
    color: var(--brand-blue);
    text-transform: uppercase;
    line-height: 1;
  }
  .card--front .wordmark {
    left: 150px;
    top: 36px;
    font-size: 30px;
    letter-spacing: 2px;
  }

  .holder-name {
    position: absolute;
    left: 34px;
    top: 148px;
    font-size: 23px;
    font-weight: 700;
    color: var(--accent-blue);
  }
  .holder-role {
    position: absolute;
    left: 44px;
    top: 180px;
    font-size: 14px;
    color: var(--ink-light);
  }
  .edge-marker {
    position: absolute;
    left: -3px;
    top: 184px;
    width: 22px;
    height: 34px;
    background: var(--accent-blue);
  }
  .divider {
    position: absolute;
    left: 64px;
    right: 32px;
    top: 208px;
    height: 1px;
    background: var(--accent-blue);
  }
  .contact-list {
    position: absolute;
    left: 44px;
    top: 222px;
    list-style: none;
  }
  .contact-list li {
    display: flex;
    align-items: center;
    gap: 8px;
    font-size: 13.5px;
    color: var(--ink-light);
    height: 24px;
  }
  .contact-list svg { width: 13px; height: 13px; fill: var(--accent-blue); flex: none; }
  .address {
    position: absolute;
    right: 36px;
    top: 226px;
    font-size: 13.5px;
    line-height: 1.55;
    color: var(--ink-light);
    font-style: normal;
  }

  .card--back .wordmark {
    left: 0;
    right: 0;
    top: 118px;
    text-align: center;
    font-size: 40px;
    letter-spacing: 3px;
    color: var(--emboss);
    text-shadow: none;
  }
</style>
</head>
<body>

  <section class="card card--front" aria-label="Business card front">
    <div class="wordmark">Tovrin Road Construction</div>

    <div class="edge-marker"></div>
    <h1 class="holder-name">Warren Halbeck</h1>
    <p class="holder-role">General Manager</p>

    <div class="divider"></div>

    <ul class="contact-list">
      <li>
        <svg viewBox="0 0 16 16" aria-hidden="true"><path d="M3.5 1.5l2.5 0 1.2 3.2-1.6 1.2a8 8 0 0 0 4.5 4.5l1.2-1.6 3.2 1.2v2.5c0 .8-.7 1.5-1.5 1.5A12.5 12.5 0 0 1 2 3c0-.8.7-1.5 1.5-1.5z"/></svg>
        0472 915 348
      </li>
      <li>
        <svg viewBox="0 0 16 16" aria-hidden="true"><path d="M1 3h14v10H1z M1 3l7 6 7-6" fill="var(--accent-blue)"/><path d="M1.5 3.5l6.5 5.5 6.5-5.5" fill="none" stroke="#161616" stroke-width="1.2"/></svg>
        Warren.halbeck@tovrin.com.au
      </li>
      <li>
        <svg viewBox="0 0 16 16" aria-hidden="true"><circle cx="8" cy="8" r="7"/><path d="M1 8h14M8 1c-3 3.5-3 10.5 0 14M8 1c3 3.5 3 10.5 0 14" fill="none" stroke="#161616" stroke-width="1"/></svg>
        www.tovrin.com.au
      </li>
    </ul>

    <address class="address">87 Marrow Ave,<br>Pendlebay, QLD, 4023</address>
  </section>

  <section class="card card--back" aria-label="Business card back">
    <div class="wordmark">Tovrin Road Construction</div>
  </section>

</body>
</html>
```